Volunteer fire fighters needed banner

As part of our recruitment campaign, we need a sign we can post on our sign trailer to entice locals to join our volunteer fire service. This design will be printed on a banner, front and back, to catch traffic going in both directions on a busy roadway. This banner will have a printed surface of 4 feet tall by 8 feet long.
Our fire department is looking to attract people between the ages of 18 and 35 years old who are interested in being a firefighter. We offer our volunteers:
-Free professional training
-All equipment supplied
-Tax abatements for active volunteers
For more information, you can check us out at:
Brackenmoorfire.example

This design should:
-scale to and fit a 4'x8' canvas
-Include our web address "BrackenMoorFire.example"
-Say "Members Wanted"
-"Drill every Tuesday at 7pm"
-"57 Kestrel Pond Lane"
-Include "Bracken Moor Fire Department"

We've included reference photos and past images we use for our other campaigns for inspiration for you.

Target Market(s)

18-35 y/o

Industry/Entity Type

Fire Service

Requirements
Must have
• -scale to and fit a 4'x8' canvas -Include our web address "BrackenMoorFire.example" -Say "Members Wanted" -"Drill every Tuesday at 7pm" -"57 Kestrel Pond Lane" -Include "Bracken Moor Fire Department"

```html
<!DOCTYPE html>
<html lang="en">
<head>
<meta charset="utf-8">
<title>Members Wanted – Bracken Moor Fire Department</title>
<link rel="stylesheet" href="https://fonts.googleapis.com/css2?family=Archivo+Black&family=Montserrat:wght@700&display=swap">
<style>
  :root {
    --sky: #29a9e0;
    --navy: #1a2a6c;
    --yellow: #f7ec13;
    --white: #ffffff;
    --ink: #0d0d0d;
  }
  html, body {
    margin: 0;
    padding: 0;
    width: 1200px;
    height: 600px;
    overflow: hidden;
  }
  .banner {
    position: relative;
    width: 1200px;
    height: 600px;
    background: var(--sky);
    overflow: hidden;
    font-family: "Archivo Black", "Arial Black", sans-serif;
  }
  .footer-band {
    position: absolute;
    left: 0;
    top: 519px;
    width: 1200px;
    height: 81px;
    background: var(--navy);
  }
  .headline,
  .time,
  .address {
    position: absolute;
    left: 0;
    width: 1200px;
    margin: 0;
    text-align: center;
    line-height: 1;
    white-space: nowrap;
    paint-order: stroke fill;
    transform-origin: 600px 50%;
  }
  .headline {
    color: var(--yellow);
    font-size: 92px;
    letter-spacing: 0;
    -webkit-text-stroke: 10px var(--ink);
  }
  .headline--members { top: 65px; transform: scaleX(0.91); }
  .headline--drill { top: 162px; font-size: 96px; transform: scaleX(0.87); }
  .time,
  .address {
    color: var(--white);
    -webkit-text-stroke: 8px var(--ink);
  }
  .time { top: 282px; font-size: 84px; transform: translateX(-3px) scaleX(1.05); }
  .address { top: 366px; font-size: 58px; transform: translateX(-11px); }
  .web-address {
    position: absolute;
    left: 0;
    top: 530px;
    width: 1200px;
    margin: 0;
    text-align: center;
    font-family: "Montserrat", Arial, sans-serif;
    font-weight: 700;
    font-size: 38px;
    line-height: 1.4;
    color: var(--white);
    transform: translateX(-7px);
  }
  .brand-name {
    position: absolute;
    left: 30px;
    top: 380px;
    width: 205px;
    text-align: center;
    color: var(--white);
    font-size: 28px;
    line-height: 1.1;
    text-transform: uppercase;
  }
  .event-name {
    position: absolute;
    left: 960px;
    top: 360px;
    width: 205px;
    text-align: center;
    color: var(--yellow);
    font-size: 26px;
    line-height: 1.1;
    text-transform: uppercase;
  }
</style>
</head>
<body>
  <div class="banner">
    <div class="footer-band"></div>

    <h1 class="headline headline--members">MEMBERS WANTED</h1>
    <h2 class="headline headline--drill">DRILL EVERY TUESDAY</h2>

    <p class="time">aT 7:00 PM</p>
    <p class="address">57 Kestrel Pond Lane</p>

    <div class="brand-name">Bracken Moor Fire Department</div>
    <div class="event-name">Sam Ashby Memorial Egg Hunt</div>

    <p class="web-address">BrackenMoorFire.example</p>
  </div>
</body>
</html>
```